Business Card Design

Online clothing womens clothing store, I sell my clothing online and at the markets.

i would like the attached picture on the front of the card and the contact information on the back.

Industry/Entity Type

Business

Contact Information for Business Card

Marlow Thread
Karen Whitfield
(Instagram symbol) _marlow_thread_
(Facebook symbol) www.fakebookexample.com/marlowthreadau/

W : www.marlowthread.example.au
E : info@marlowthread.example.au
P : 0498716204

```html
<!DOCTYPE html>
<html lang="en">
<head>
<meta charset="utf-8">
<title>Marlow Thread – Business Card</title>
<link rel="stylesheet" href="https://fonts.googleapis.com/css2?family=Josefin+Sans:wght@300&family=Roboto:wght@300;400&display=swap">
<style>
  :root {
    --page-bg: #e4e2df;
    --card-white: #f4f4f4;
    --card-white-shade: #dcdcdc;
    --card-black: #0c0c0c;
    --ink-dark: #1a1a1a;
    --ink-light: #ffffff;
    --photo-light: #d7dadc;
    --photo-mid: #8d8f9a;
    --photo-dark: #4d4a5a;
  }
  * { margin: 0; padding: 0; box-sizing: border-box; }
  html, body {
    width: 1200px; height: 892px; overflow: hidden;
    background: var(--page-bg);
  }
  .sheet {
    width: 1200px; height: 892px;
    display: flex; flex-direction: column; align-items: center; justify-content: center;
    gap: 56px;
  }
  .card {
    width: 640px; height: 380px;
    border-radius: 22px;
    overflow: hidden;
    box-shadow: 0 10px 28px rgba(0,0,0,0.18);
    position: relative;
  }

  /* Contact side */
  .card-contact { display: flex; flex-direction: column; }
  .brand-band {
    flex: 0 0 46%;
    background: linear-gradient(180deg, var(--card-white) 0%, var(--card-white) 55%, var(--card-white-shade) 100%);
    display: flex; align-items: flex-end; justify-content: center;
    padding-bottom: 34px;
  }
  .brand-name {
    font-family: "Josefin Sans", sans-serif;
    font-weight: 300;
    font-size: 50px;
    letter-spacing: 10px;
    color: var(--ink-dark);
    text-transform: uppercase;
  }
  .info-band {
    flex: 1;
    background: var(--card-black);
    display: flex; align-items: center;
    padding: 0 34px;
  }
  .holder-name {
    font-family: "Josefin Sans", sans-serif;
    font-weight: 300;
    font-size: 27px;
    letter-spacing: 3px;
    color: var(--ink-light);
    width: 260px;
    align-self: flex-end;
    padding-bottom: 40px;
  }
  .divider {
    width: 2px; height: 160px;
    background: var(--ink-light);
    margin: 0 26px 0 0;
  }
  .contact-list { list-style: none; }
  .contact-item {
    display: flex; align-items: center; gap: 10px;
    font-family: "Roboto", sans-serif;
    font-weight: 400;
    font-size: 16px;
    color: var(--ink-light);
    line-height: 30px;
  }
  .contact-icon { width: 14px; height: 14px; flex: 0 0 14px; }

  /* Photo side */
  .card-photo {
    background:
      radial-gradient(ellipse at 30% 40%, var(--photo-dark) 0%, transparent 55%),
      radial-gradient(ellipse at 75% 70%, var(--photo-mid) 0%, transparent 60%),
      linear-gradient(160deg, var(--photo-light) 0%, var(--photo-mid) 55%, var(--photo-light) 100%);
    display: flex; align-items: flex-end; justify-content: center;
    padding-bottom: 50px;
  }
  .photo-brand {
    font-family: "Josefin Sans", sans-serif;
    font-weight: 300;
    font-size: 60px;
    letter-spacing: 6px;
    color: var(--ink-light);
    text-transform: uppercase;
  }
</style>
</head>
<body>
<main class="sheet">
  <section class="card card-contact">
    <div class="brand-band">
      <span class="brand-name">Marlow Thread</span>
    </div>
    <div class="info-band">
      <p class="holder-name">Karen Whitfield</p>
      <span class="divider"></span>
      <ul class="contact-list">
        <li class="contact-item">
          <svg class="contact-icon" viewBox="0 0 14 14"><rect width="14" height="14" fill="#fff"/><path d="M4 3.5 L5.5 3.5 L6 5.5 L5 6.2 Q6 8.2 7.8 9 L8.5 8 L10.5 8.5 L10.5 10 Q6 10.5 3.5 5 Z" fill="#0c0c0c"/></svg>
          <span>0498716204</span>
        </li>
        <li class="contact-item">
          <svg class="contact-icon" viewBox="0 0 14 14"><rect width="14" height="14" fill="#fff"/><rect x="3" y="4.5" width="8" height="5.5" fill="none" stroke="#0c0c0c" stroke-width="1"/><path d="M3 4.5 L7 7.5 L11 4.5" fill="none" stroke="#0c0c0c" stroke-width="1"/></svg>
          <span>info@marlowthread.example.au</span>
        </li>
        <li class="contact-item">
          <svg class="contact-icon" viewBox="0 0 14 14"><rect width="14" height="14" fill="#fff"/><circle cx="7" cy="7" r="3.8" fill="none" stroke="#0c0c0c" stroke-width="1"/><path d="M3.2 7 H10.8 M7 3.2 V10.8" stroke="#0c0c0c" stroke-width="0.8"/></svg>
          <span>www.marlowthread.example.au</span>
        </li>
        <li class="contact-item">
          <svg class="contact-icon" viewBox="0 0 14 14"><rect width="14" height="14" fill="#fff"/></svg>
          <span>marlowthreadau</span>
        </li>
        <li class="contact-item">
          <svg class="contact-icon" viewBox="0 0 14 14"><rect width="14" height="14" fill="#fff"/></svg>
          <span>marlow_thread</span>
        </li>
      </ul>
    </div>
  </section>

  <section class="card card-photo" role="img" aria-label="Misty grey and violet watercolour-style photograph of clouds behind the brand name">
    <span class="photo-brand">Marlow Thread</span>
  </section>
</main>
</body>
</html>
```